Marlowe Group needs a business card

I would like the card to be simple but modern and elegant.
I like black and white.
or black and gold.
we are a private finance lender and also are involved in property and property developments.

please look at the business card photos i provided i would like M.G only one one side and all the other details on the other side use fonts that tie in with my theme.

Industry/Entity Type

Finance

Contact Information for Business Card

Marlowe Group (M.G) Daniel Marlowe M: 0413586207 E: danmarl@inboxmail.test

Font styles to use
Other font styles liked:
• Use fonts that would reflect our business

Colors
000000
ffffff

Requirements
Must have
• one side of details
• other side has either M.G or Marlowe Group like in the photos provided

```html
<!DOCTYPE html>
<html lang="en">
<head>
<meta charset="utf-8">
<title>Marlowe Group – Business Card</title>
<link href="https://fonts.googleapis.com/css2?family=Open+Sans:wght@400;600;700;800&display=swap" rel="stylesheet">
<style>
  :root {
    --ink: #000000;
    --paper: #ffffff;
    --gold: #f6a21d;
    --backdrop: #c9c7c6;
  }
  * { margin: 0; padding: 0; box-sizing: border-box; }
  html, body {
    width: 1200px; height: 1011px; overflow: hidden;
    background: var(--backdrop);
    font-family: "Open Sans", Arial, sans-serif;
  }
  .canvas { position: relative; width: 1200px; height: 1011px; }

  .card {
    position: absolute;
    width: 760px; height: 434px;
    overflow: hidden;
    box-shadow: 0 18px 40px rgba(0,0,0,0.28);
  }
  .card--back { left: 90px; top: 50px; background: var(--ink); }
  .card--front { left: 350px; top: 527px; background: var(--paper); }

  .card__art { position: absolute; inset: 0; width: 100%; height: 100%; }

  .wordmark {
    position: absolute;
    display: flex; align-items: baseline;
    line-height: 1;
    letter-spacing: -0.02em;
  }
  .wordmark__name { font-weight: 800; font-size: 66px; }
  .wordmark__group {
    font-weight: 700; font-size: 30px; margin-left: 10px;
    letter-spacing: 0;
  }
  .card--back .wordmark { left: 225px; top: 168px; color: var(--paper); }
  .card--back .wordmark__group {
    padding-bottom: 6px;
    border-bottom: 1.5px solid var(--paper);
    padding-right: 6px;
  }
  .card--front .wordmark { left: 105px; top: 160px; color: var(--ink); }

  .holder {
    position: absolute; left: 28px; bottom: 8px;
    color: var(--paper); font-weight: 600; font-size: 27px;
    letter-spacing: 0.01em;
  }
  .contacts {
    position: absolute; left: 420px; top: 348px;
    list-style: none; color: var(--paper);
    font-size: 20px; font-weight: 400;
  }
  .contacts li { display: flex; align-items: center; gap: 12px; margin-bottom: 10px; }
  .contacts__icon {
    width: 24px; height: 24px; border-radius: 4px;
    background: var(--gold);
    display: flex; align-items: center; justify-content: center;
    flex-shrink: 0;
  }
</style>
</head>
<body>
<main class="canvas">

  <!-- Reverse side: wordmark only -->
  <section class="card card--back" aria-label="Card reverse">
    <svg class="card__art" viewBox="0 0 760 434" aria-hidden="true">
      <rect x="425" y="-20" width="350" height="38" rx="12" fill="var(--gold)"/>
      <rect x="-15" y="416" width="345" height="38" rx="12" fill="var(--gold)"/>
    </svg>
    <div class="wordmark">
      <span class="wordmark__name">Marlowe</span>
      <span class="wordmark__group">Group</span>
    </div>
  </section>

  <!-- Face side: details -->
  <section class="card card--front" aria-label="Card face">
    <svg class="card__art" viewBox="0 0 760 434" aria-hidden="true">
      <rect x="415" y="-20" width="360" height="40" rx="12" fill="var(--gold)"/>
      <line x1="490" y1="170" x2="748" y2="170" stroke="var(--ink)" stroke-width="1.2"/>
      <rect x="-15" y="376" width="325" height="40" rx="12" fill="var(--gold)"/>
      <polygon points="0,396 330,396 385,335 760,335 760,434 0,434" fill="var(--ink)"/>
      <polygon points="388,342 470,342 462,352 380,352" fill="var(--paper)"/>
    </svg>

    <div class="wordmark">
      <span class="wordmark__name">Marlowe</span>
      <span class="wordmark__group">Group</span>
    </div>

    <p class="holder">Daniel Marlowe</p>

    <ul class="contacts">
      <li>
        <span class="contacts__icon">
          <svg width="14" height="14" viewBox="0 0 14 14" aria-hidden="true">
            <rect x="3.5" y="1" width="7" height="12" rx="1.2" fill="none" stroke="var(--ink)" stroke-width="1.4"/>
            <rect x="5.5" y="10.2" width="3" height="1.2" fill="var(--ink)"/>
          </svg>
        </span>
        <span>0413586207</span>
      </li>
      <li>
        <span class="contacts__icon">
          <svg width="14" height="14" viewBox="0 0 14 14" aria-hidden="true">
            <rect x="1" y="3" width="12" height="8" fill="none" stroke="var(--ink)" stroke-width="1.3"/>
            <polyline points="1,3 7,8 13,3" fill="none" stroke="var(--ink)" stroke-width="1.3"/>
          </svg>
        </span>
        <span>danmarl@inboxmail.test</span>
      </li>
    </ul>
  </section>

</main>
</body>
</html>
```